Brightfen Business Card Redesign & Logo Update

We need to update our business cards to something more modern and fresh. Brightfen can provide the current color schemes and old design examples, but welcome creativity in helping us with this redesign. PLEASE NOTE that we no longer utilize the "tree" and/or "leaf" imagery in our branding. If able would apprecaite an update on the quality of our "words only" logo in Ai. / PNG formats too.

Target Market(s)

Investors, landowners, corporate partners, contractors

Industry/Entity Type

Environmental Restoration & Conservation

Contact Information for Business Card

Logo, persons name, title, mailing address, phone and email, website url

Font styles to use
Other font styles liked:
• Merriweather

Requirements
Nice to have
• Logo, persons name, title, mailing address, phone and email, website url, but open to ideams
Should not have
• No all back backgrounds

```html
<!DOCTYPE html>
<html lang="en">
<head>
<meta charset="UTF-8">
<title>Brightfen Business Card</title>
<link href="https://fonts.googleapis.com/css2?family=Open+Sans:wght@400;600;700;800&display=swap" rel="stylesheet">
<style>
  :root {
    --stage: #e9eaec;
    --card: #ffffff;
    --orange: #e87e24;
    --green: #138240;
    --ink: #1b1b1b;
    --rule: #222222;
  }
  * { margin: 0; padding: 0; box-sizing: border-box; }
  html, body { width: 1200px; height: 780px; overflow: hidden; }
  body {
    background: var(--stage);
    font-family: "Open Sans", Arial, sans-serif;
    position: relative;
  }
  .card {
    position: absolute;
    width: 560px;
    height: 320px;
    background: var(--card);
    box-shadow: 0 6px 18px rgba(0,0,0,0.18);
  }
  .card-front { left: 60px; top: 60px; }
  .card-back { left: 580px; top: 400px; }

  .wordmark {
    font-family: "Open Sans", Arial, sans-serif;
    font-weight: 800;
    color: var(--green);
    text-transform: uppercase;
    letter-spacing: 1px;
    line-height: 1;
  }
  .card-front .wordmark {
    position: absolute;
    left: 0; right: 0; top: 118px;
    text-align: center;
    font-size: 74px;
  }
  .card-back .wordmark {
    position: absolute;
    left: 34px; top: 40px;
    font-size: 40px;
  }

  .holder {
    position: absolute;
    right: 30px; top: 112px;
    text-align: right;
  }
  .holder-name {
    font-weight: 700;
    font-size: 26px;
    line-height: 1.1;
    letter-spacing: 0.5px;
  }
  .holder-name .first { color: var(--orange); }
  .holder-name .last { color: var(--green); }
  .holder-title {
    font-size: 14px;
    color: var(--ink);
    margin-top: 2px;
    padding-right: 4px;
  }
  .divider {
    position: absolute;
    left: 110px; right: 22px; top: 176px;
    height: 1.5px;
    background: var(--rule);
  }
  .contacts {
    position: absolute;
    left: 150px; top: 200px;
    list-style: none;
  }
  .contact {
    display: flex;
    align-items: center;
    gap: 10px;
    font-size: 15px;
    color: var(--ink);
    height: 26px;
  }
  .contact svg { width: 16px; height: 16px; flex: none; }
</style>
</head>
<body>
  <section class="card card-front" aria-label="Business card front">
    <div class="wordmark">Brightfen</div>
  </section>

  <section class="card card-back" aria-label="Business card back">
    <div class="wordmark">Brightfen</div>

    <div class="holder">
      <div class="holder-name"><span class="first">Lena</span> <span class="last">Marsh</span></div>
      <div class="holder-title">Managing Director</div>
    </div>

    <div class="divider"></div>

    <ul class="contacts">
      <li class="contact">
        <svg viewBox="0 0 16 16" aria-hidden="true"><path fill="#e87e24" d="M3.6 1.5l2.3 2.6-1.3 1.6c.9 2 2.5 3.7 4.6 4.7l1.6-1.3 2.7 2.2-1.2 2.3C7.5 13.4 2.4 8.4 1.9 3z"/></svg>
        <span>(555) 014-2290</span>
      </li>
      <li class="contact">
        <svg viewBox="0 0 16 16" aria-hidden="true"><rect x="1.5" y="3.5" width="13" height="9" rx="1" fill="#e87e24"/><path d="M2 4.2l6 4.6 6-4.6" fill="none" stroke="#fff" stroke-width="1.3"/></svg>
        <span>hello@brightfen-mail.com</span>
      </li>
      <li class="contact">
        <svg viewBox="0 0 16 16" aria-hidden="true"><circle cx="8" cy="8" r="6.5" fill="#e87e24"/><path d="M1.5 8h13M8 1.5c-3 3.5-3 9.5 0 13M8 1.5c3 3.5 3 9.5 0 13" fill="none" stroke="#fff" stroke-width="1"/></svg>
        <span>www.brightfen-site.com</span>
      </li>
    </ul>
  </section>
</body>
</html>
```